Velvet Harbor Snout Sticks - our own unique product line of cotton swabs

We have something now that we are not too happy with. Looking to create a label for a line of cotton swabs that we have created and designed to clean your nose from mucus and boogers. The logo that i have so far for the packaging is the white background with the black silhouette nose (attached). We need something that can do well in the retail/consumer market. Our website address (even though it is not live yet) should be listed somewhere on the label....
www.VelvetHarborGoods.example ( we sell pillows, but we have other product lines)
We would also like to see a brief description on how to correctly use the nose pick on the back side of the label. The description on how to use should read " insert cotton nose pick into nostril and give it a few counter clock wise twirls or till you feel mucus/debris latch onto the cotton. You may need to repeat the process and use more than one nose pick to achieve desired result."
As well as a warning mentioning : "Never insert plastic end of nose pick into any part of your body. Be careful and use with caution."
Also for you to know, the cotton is made from 100% natural cotton, the cotton head itself is thick and highly absorbent making it a pleasure to use. There are 50 nose picks per pack.
We're fine with keeping it simple and not making the packaging too busy, however we're open to your ideas and designs! I have given you the most important information relevant to the project. If there are any questions or something is not clear enough please kindly message me.

Requirements
Must have
• professional looking
clean looking
not busy
Should not have
• words clumping together making it appear as too much text in one area
too much text clumped together on the design

```html
<!DOCTYPE html>
<html lang="en">
<head>
<meta charset="utf-8">
<title>Velvet Harbor Snout Sticks – Cotton Swab Label</title>
<link rel="stylesheet" href="https://fonts.googleapis.com/css2?family=Montserrat:wght@300;400;600;700;800&display=swap">
<style>
  :root {
    --teal: #3fb5a8;
    --teal-deep: #2ea396;
    --teal-pale: #d6efeb;
    --slate: #8b9096;
    --slate-dark: #6c7278;
    --ink: #5f656b;
    --paper: #ffffff;
    --stage: #f4f5f6;
  }
  * { box-sizing: border-box; margin: 0; padding: 0; }
  html, body { width: 1200px; height: 679px; overflow: hidden; }
  body {
    background: var(--stage);
    font-family: "Montserrat", sans-serif;
    color: var(--ink);
    display: flex;
    align-items: center;
    justify-content: center;
    gap: 40px;
  }
  .label {
    position: relative;
    width: 540px;
    height: 420px;
    background: var(--paper);
    box-shadow: 0 2px 10px rgba(0,0,0,0.08);
    overflow: hidden;
  }

  /* Front panel */
  .brand {
    position: absolute;
    left: 40px; top: 48px;
    display: flex; align-items: center; gap: 14px;
  }
  .brand-dot {
    width: 26px; height: 26px; border-radius: 50%;
    background: var(--slate);
  }
  .brand-name {
    font-size: 30px; font-weight: 600; color: var(--slate);
    line-height: 1;
  }
  .brand-line {
    position: absolute; left: 80px; top: 112px;
    font-size: 11px; font-weight: 400; letter-spacing: 4px; color: var(--slate-dark);
  }
  .seal { position: absolute; right: 36px; top: 24px; width: 104px; height: 104px; }
  .headline-small {
    position: absolute; left: 40px; top: 178px;
    font-size: 20px; font-weight: 700; letter-spacing: 2.5px; color: var(--slate-dark);
  }
  .band-main {
    position: absolute; left: 0; top: 214px; width: 100%; height: 70px;
    background: var(--teal);
  }
  .band-main .title {
    position: absolute; left: 40px; top: 10px;
    font-size: 42px; font-weight: 800; color: var(--paper); letter-spacing: 0.5px;
    white-space: nowrap;
  }
  .count {
    position: absolute; right: 12px; top: 6px; text-align: center;
    color: var(--paper); line-height: 1;
  }
  .count .num { font-size: 34px; font-weight: 800; display: block; }
  .count .unit { font-size: 14px; font-weight: 600; }
  .band-sub {
    position: absolute; left: 0; top: 284px; width: 80%; height: 34px;
    background: var(--slate);
  }
  .band-sub .tagline {
    position: absolute; left: 40px; top: 9px;
    font-size: 12.5px; font-weight: 700; letter-spacing: 1.2px; color: var(--paper);
    white-space: nowrap;
  }
  .swab-art {
    position: absolute; left: 440px; top: 160px; width: 36px; height: 220px;
    background: linear-gradient(180deg, rgba(139,144,150,0.18), rgba(139,144,150,0.32));
    border-radius: 18px;
  }
  .site {
    position: absolute; left: 40px; bottom: 34px;
    font-size: 15px; font-weight: 700; letter-spacing: 0.8px; color: var(--teal);
  }

  /* Back panel */
  .howto-head {
    position: absolute; left: 40px; right: 40px; top: 40px;
    display: flex; align-items: center; gap: 10px;
  }
  .howto-head .rule { flex: 1; border-top: 3px dotted var(--teal); }
  .howto-head h2 {
    font-size: 17px; font-weight: 700; letter-spacing: 1.5px; color: var(--teal);
  }
  .steps {
    position: absolute; left: 0; right: 0; top: 76px;
    display: flex; justify-content: center; gap: 26px;
  }
  .step {
    width: 70px; height: 70px; border-radius: 50%;
    border: 3px solid var(--teal); background: var(--teal-pale);
  }
  .instructions {
    position: absolute; left: 70px; right: 70px; top: 172px;
    text-align: center; font-size: 14.5px; font-weight: 400; line-height: 1.55;
  }
  .warning {
    position: absolute; left: 70px; right: 70px; bottom: 26px;
    border: 2px solid var(--teal); border-radius: 10px;
    padding: 8px 14px; text-align: center;
    font-size: 13.5px; line-height: 1.4;
  }
</style>
</head>
<body>

  <section class="label label-front" aria-label="Front of label">
    <div class="brand">
      <span class="brand-dot"></span>
      <span class="brand-name">Velvet Harbor</span>
    </div>
    <div class="brand-line">Snout Sticks</div>

    <svg class="seal" viewBox="0 0 104 104" aria-label="Natural cotton, highly absorbent seal">
      <defs>
        <path id="seal-arc" d="M52,52 m-33,0 a33,33 0 1,1 66,0 a33,33 0 1,1 -66,0"/>
      </defs>
      <circle cx="52" cy="52" r="50" fill="var(--teal)"/>
      <circle cx="52" cy="52" r="46" fill="none" stroke="#ffffff" stroke-width="1" stroke-dasharray="2 3"/>
      <text font-family="Montserrat, sans-serif" font-size="7" font-weight="700" fill="#ffffff" textLength="200" lengthAdjust="spacing">
        <textPath href="#seal-arc" textLength="200" lengthAdjust="spacing">NATURAL COTTON · HIGHLY ABSORBENT ·</textPath>
      </text>
      <circle cx="52" cy="52" r="22" fill="#bfe5df" role="img" aria-label="Cotton boll illustration"/>
    </svg>

    <p class="headline-small">100% NATURAL COTTON</p>
    <div class="band-main">
      <h1 class="title">COTTON SWABS</h1>
      <div class="count"><span class="num">50</span><span class="unit">units</span></div>
    </div>
    <div class="band-sub">
      <p class="tagline">CLEAN YOUR NOSE FROM MUCUS AND BOOGERS</p>
    </div>
    <div class="swab-art" role="img" aria-label="Two crossed cotton swabs illustration"></div>
    <p class="site">www.VelvetHarborGoods.example</p>
  </section>

  <section class="label label-back" aria-label="Back of label">
    <div class="howto-head">
      <span class="rule"></span>
      <h2>HOW TO USE</h2>
      <span class="rule"></span>
    </div>
    <div class="steps">
      <div class="step" role="img" aria-label="Step 1: insert swab into nostril"></div>
      <div class="step" role="img" aria-label="Step 2: twirl swab counter clockwise"></div>
      <div class="step" role="img" aria-label="Step 3: remove swab with debris"></div>
    </div>
    <p class="instructions">
      Insert cotton nose pick into nostril and give it a few counter clock wise twirls or till you feel mucus/debris latch onto the cotton. You may need to repeat the process and use more than one nose pick to achieve desired result.
    </p>
    <p class="warning">
      Never insert plastic end of nose pick into any part of your body. Be careful and use with caution.
    </p>
  </section>

</body>
</html>
```